Web Developer Needs a Business Card Design

I need a personal business card design that represents me as a web developer for potential employers. I would like the background to be a dark color on the front for contrast with my logo and name. The back will have all my information along with a smaller version of the logo. I want something with a modern look and feel, not too conservative. This will be used for potential employers and freelance work.

Industry/Entity Type

Business

Contact Information for Business Card

Front should have my logo and name. The back should have all my personal information which would include: name: Tom Varulek, phone: 570-614-3098, email: tomvarulek@quillbox.net, website url: www.tomvarulek.net, logo, web developer.

Font styles to use
Sans Serif

Requirements
Must have
• Must include my logo. The color palette base color will be the logo color.

```html
<!DOCTYPE html>
<html lang="en">
<head>
<meta charset="utf-8">
<title>Tom Varulek — Web Developer Business Card</title>
<link rel="stylesheet" href="https://fonts.googleapis.com/css2?family=Source+Sans+3:wght@400;700&display=swap">
<style>
  :root {
    --mint: #8bcab9;
    --charcoal: #363636;
    --paper: #ffffff;
  }
  html, body {
    margin: 0;
    padding: 0;
    width: 1200px;
    height: 686px;
    overflow: hidden;
    background: var(--paper);
  }
  .business-card {
    display: block;
    width: 1200px;
    height: 686px;
    font-family: "Source Sans 3", "Myriad Pro", sans-serif;
  }
  .band-top { fill: var(--mint); }
  .band-gap { fill: var(--paper); }
  .card-body { fill: var(--charcoal); }
  .brand-ring { fill: none; stroke: var(--mint); stroke-width: 13; }
  .brand-name {
    fill: var(--mint);
    font-weight: 700;
    font-size: 30px;
  }
  .holder-name {
    fill: var(--mint);
    font-weight: 700;
    font-size: 52px;
    letter-spacing: 0.5px;
  }
  .holder-role {
    fill: var(--paper);
    font-weight: 400;
    font-size: 30px;
  }
  .contact-label {
    fill: var(--mint);
    font-weight: 400;
    font-size: 29px;
  }
  .contact-value {
    fill: var(--paper);
    font-weight: 400;
    font-size: 29px;
  }
</style>
</head>
<body>
<svg class="business-card" viewBox="0 0 1200 686" xmlns="http://www.w3.org/2000/svg" role="img" aria-label="Business card of Tom Varulek, web developer">
  <rect class="band-top" x="0" y="0" width="1200" height="77"/>
  <rect class="band-gap" x="0" y="77" width="1200" height="51"/>
  <rect class="card-body" x="0" y="128" width="1200" height="558"/>

  <g class="brand-mark">
    <circle class="brand-ring" cx="163" cy="514" r="94"/>
    <text class="brand-name" x="163" y="524" text-anchor="middle">Varulek</text>
  </g>

  <text class="holder-name" x="315" y="465">TOM VARULEK</text>
  <text class="holder-role" x="725" y="467">//&#160;&#160;WEB DEVELOPER</text>

  <g class="contact-list">
    <text class="contact-label" x="318" y="518">Mobile</text>
    <text class="contact-value" x="448" y="518">570-614-3098</text>

    <text class="contact-label" x="318" y="564">Email</text>
    <text class="contact-value" x="448" y="564">tomvarulek@quillbox.net</text>

    <text class="contact-label" x="318" y="609">Website</text>
    <text class="contact-value" x="448" y="609">www.tomvarulek.net</text>
  </g>
</svg>
</body>
</html>
```